Company selling food supplements with CBD needs label.

We need a label design for a company called "VEKA Works ltd", is based in the UK, the market name is "QELVO" or "VEKA Very Easy Kindly Aged". The initial product is Virgin Organic Hemp Seed Oil with a CBD in a 10ml amber dropper bottle. The design should be simplicity and luxury. The design should include also box.

Target Market(s)

Food supplements on Tradeshelf UK

Industry/Entity Type

Supplement

Font styles to use
Other font styles liked:
• Some luxury

Colors

Designer to choose colors to be used in the design.

Requirements
Must have
• All the information on the label required by the UK for the food supplements, the same on the box. One version matt one transparent. The design should include different CBD content, one different bottle (250mg, 500mg, 750mg, 1000mg) .
• The label and box should include the following phrases: "DIRECTIONS: Food Supplement. Shake well before use. Use 4-6 drops 2-3 times a day. Leave the oil in your mouth for 30-60 seconds before swallowing. Gradually build up the dose to find your optimum dosage.
• CAUTION: Do not exceed the recommended daily intake. Do not use as a substitute for a varied diet. Do not use during pregnancy and breastfeeding. Store in a dark and cool place, away from sunlight. Keep away from children.
• INGREDIENTS: Hemp Seed Oil, Omega-6 (2800mg), Omega-3 (930mg), CBD (250mg)
• MANUFACTURED: QELVO Labs Ltd, 87 Pelbury Rd, Harrow, HA7 2QX, www,vekaworks.example, info@qelvolabs.example.
• EXPIRED DATE: "
• The box should also include a place for bark code.
Nice to have
• Simple and elegant design vertical or horizontal with exposed company logo "QELVO" or "VEKA Very Easy Kindly Aged". The company logo is provided but designers may change it freely.
Should not have
• The best without pictures/graphics overloading simplicity and purity of design.

```html
<!DOCTYPE html>
<html lang="en">
<head>
<meta charset="utf-8">
<title>QELVO – Hemp Seed Oil Box</title>
<link href="https://fonts.googleapis.com/css2?family=Questrial&family=Oswald:wght@400;500&family=Archivo+Narrow:wght@700&display=swap" rel="stylesheet">
<style>
  :root{
    --bg-light:#e9e9e9;
    --bg-dark:#8f8f8f;
    --panel-black:#020a06;
    --panel-green:#0b3a22;
    --glow-green:#0f8a48;
    --accent-line:#1fa35a;
    --leaf-green:#2f6b34;
    --pill-green:#6fc477;
    --pill-text:#06210f;
    --text-white:#ffffff;
    --batch-white:#ffffff;
    --batch-text:#000000;
  }
  *{box-sizing:border-box;margin:0;padding:0}
  html,body{width:1200px;height:1020px;overflow:hidden}
  body{
    background:radial-gradient(ellipse at 50% 45%,var(--bg-light) 0%,var(--bg-dark) 100%);
    font-family:"Questrial",sans-serif;
    color:var(--text-white);
    position:relative;
  }
  .box-net{position:absolute;left:80px;top:90px;width:1040px;height:840px}
  .panel{
    position:absolute;top:240px;width:260px;height:600px;overflow:hidden;
    background:radial-gradient(ellipse at 60% 50%,var(--panel-green) 0%,var(--panel-black) 70%);
    border-right:1px solid rgba(255,255,255,.08);
  }
  .panel::before,.panel::after{
    content:"";position:absolute;left:0;right:0;height:2px;
    background:linear-gradient(90deg,transparent,var(--accent-line),transparent);
  }
  .panel::before{top:14px}
  .panel::after{bottom:14px}
  .panel-caution{left:0}
  .panel-brand{left:260px;background:radial-gradient(ellipse at 30% 60%,var(--glow-green) 0%,var(--panel-green) 30%,var(--panel-black) 72%)}
  .panel-product{left:520px}
  .panel-directions{left:780px}

  .lid{
    position:absolute;left:260px;top:0;width:260px;height:240px;
    background:radial-gradient(ellipse at 50% 40%,var(--panel-green) 0%,var(--panel-black) 75%);
    border-bottom:1px solid rgba(255,255,255,.15);
    display:flex;flex-direction:column;align-items:center;justify-content:center;
  }
  .lid-wordmark{font-size:60px;letter-spacing:3px;line-height:1}
  .lid-tagline{font-family:"Oswald",sans-serif;font-size:15px;margin-top:10px;letter-spacing:.5px}

  .volume{position:absolute;left:18px;top:34px;font-size:20px}
  .caution{position:absolute;left:18px;top:96px;width:228px;font-size:15.5px;line-height:1.22}
  .maker{position:absolute;left:18px;bottom:40px;width:230px;font-size:14px;line-height:1.25}
  .maker-name{font-size:20px;line-height:1.1;margin:2px 0}

  .brand-vertical{
    position:absolute;left:50%;top:50%;width:580px;
    transform:translate(-50%,-50%) rotate(-90deg);
    display:flex;flex-direction:column;align-items:center;
  }
  .brand-word{font-size:140px;line-height:.9;letter-spacing:4px}
  .brand-tagline{font-family:"Oswald",sans-serif;font-size:28px;letter-spacing:.5px;margin-top:8px}

  .leaf-art{
    position:absolute;left:55px;top:70px;width:150px;height:190px;
    background:radial-gradient(ellipse at 50% 55%,var(--leaf-green) 0%,rgba(47,107,52,.25) 55%,transparent 75%);
  }
  .product-name{position:absolute;left:0;right:0;top:290px;text-align:center;font-size:30px;line-height:1.1}
  .strength{
    position:absolute;left:50%;top:440px;transform:translateX(-50%);
    background:var(--pill-green);color:var(--pill-text);border-radius:24px;
    padding:6px 22px;font-family:"Oswald",sans-serif;font-weight:500;font-size:30px;white-space:nowrap;
  }

  .info{position:absolute;left:16px;top:36px;width:232px;font-size:14.5px;line-height:1.2}
  .info-heading{font-size:21px;margin-bottom:2px}
  .info-block{padding:6px 0;border-bottom:1px solid var(--accent-line)}
  .info-block:last-child{border-bottom:none}
  .ingredients td{padding-right:8px}
  .batch{
    position:absolute;left:16px;right:16px;bottom:36px;height:120px;
    background:var(--batch-white);color:var(--batch-text);
    display:flex;align-items:center;justify-content:center;
    font-family:"Archivo Narrow",sans-serif;font-weight:700;font-style:italic;font-size:54px;
  }
</style>
</head>
<body>
  <main class="box-net">
    <section class="lid">
      <div class="lid-wordmark">QELVO</div>
      <div class="lid-tagline">Quiet Earth Leaf Vital Oils</div>
    </section>

    <section class="panel panel-caution">
      <div class="volume">10 Ml.</div>
      <div class="caution">
        CAUTION:<br>
        Do not exceed the recommended daily intake.<br>
        Do not use as a substitute for a varied diet.<br>
        Do not use during pregnancy and breastfeeding.<br>
        Store in a dark and cool place, away from sunlight.<br>
        Keep away from children.
      </div>
      <div class="maker">
        MANUFACTURED BY:
        <div class="maker-name">QELVO LABS LTD.</div>
        Pelbury Rd, Dunmarsh,<br>
        DM4 7QX<br>
        www.qelvolabs.example,<br>
        info@qelvolabs.example
      </div>
    </section>

    <section class="panel panel-brand">
      <div class="brand-vertical">
        <div class="brand-word">QELVO</div>
        <div class="brand-tagline">Quiet Earth Leaf Vital Oils</div>
      </div>
    </section>

    <section class="panel panel-product">
      <div class="leaf-art" role="img" aria-label="Green hemp leaf illustration"></div>
      <div class="product-name">Virgin<br>Organic<br>Hemp seed Oil</div>
      <div class="strength">CBD 250mg</div>
    </section>

    <section class="panel panel-directions">
      <div class="info">
        <div class="info-block">
          <div class="info-heading">DIRECTIONS:</div>
          Food Supplement.<br>
          Shake well before use.<br>
          Use 4-6 drops 2-3 times a day.<br>
          Leave the oil in your mouth for 30-60 Seconds before swallowing.<br>
          Gradually build up the dose to find your optimum dosage.
        </div>
        <div class="info-block">
          <div class="info-heading">INGREDIENTS:</div>
          <table class="ingredients">
            <tr><td colspan="2">Hemp Seed Oil</td></tr>
            <tr><td>Omega-6</td><td>-- 2800mg</td></tr>
            <tr><td>Omega-3</td><td>-- 930mg</td></tr>
            <tr><td>CBD</td><td>-- 250mg</td></tr>
          </table>
        </div>
        <div class="info-block">
          <table class="ingredients">
            <tr><td>Date of Mfg.</td><td>18.12.2019</td></tr>
            <tr><td>Date of Exp.</td><td>18-12-2021</td></tr>
          </table>
        </div>
      </div>
      <div class="batch">Batch</div>
    </section>
  </main>
</body>
</html>
```